kolvarin.link kolvarin.space kolvarin.press website

The website is named KOLVARIN and it will have 3 domain names. kolvarin.link, press, space.
I'd like it to be viewed on Pads, pcs and phones.

page menu:

kolvarin.link(start page): presentation of company. (creative, design, app, new product innovation.)
Here we'll need sosial media icons: plimber, vendoloop, mirtavel, trelvanet. (light but some 'fruity' colors)

kolvarin.press: blog. It will be a 75% picture blog > rest will be text. I need to be able to resize pictures and shape columns to picture size. (light but some 'fruity' colors)

kolvarin.space : the fun part of this web design, however, on entering the page I'd like a non-disclosure agreement where viewer simply click "yes, I agree" after filling out contact info. (check attached document)
We will have space here for uploading PDF files viewers can download. There is also a blog space here to tell in brief about the PDF file. (maybe a space/sci-fi theme her e.g spacechimp, Laika the space dog?)

I will attach the logo here I want you to use > and develop for the .space .press webpage. The logo i uploaded is for the .link page.

Target Market(s)

venture capitalists

Number of Pages Required

3 page

Requirements
Must have
• a few 'fruity colors' but mostly white and grey

```html
<!DOCTYPE html>
<html lang="en">
<head>
<meta charset="utf-8">
<title>KOLVARIN LINK</title>
<link rel="stylesheet" href="https://fonts.googleapis.com/css2?family=Lato:ital,wght@0,400;0,700;0,900;1,400;1,700&family=Ubuntu:wght@500&display=swap">
<style>
:root{
  --orange:#f27121;
  --orange-dark:#d9581a;
  --amber:#f8a51c;
  --ink:#111111;
  --text:#222222;
  --green:#6a9a3a;
  --grey-bg:#f1f1f1;
  --card-text:#d4d4d4;
  --footer:#2b2b2b;
  --footer-text:#9a9a9a;
  --hero-blue:#2a6aa3;
  --white:#ffffff;
}
*{box-sizing:border-box;margin:0;padding:0}
html,body{width:940px;height:1200px;overflow:hidden}
body{position:relative;font-family:"Lato",sans-serif;color:var(--text);background:var(--white)}
.abs{position:absolute}

/* header */
.site-header{left:0;top:0;width:940px;height:81px;background:linear-gradient(#ffffff,#f4f4f4)}
.brand{left:40px;top:22px;display:flex;align-items:center;gap:7px}
.brand-mark{width:14px;height:14px;background:var(--orange)}
.brand-name{font-family:"Lato",sans-serif;font-weight:900;font-size:22px;color:var(--ink);letter-spacing:.5px}
.contact{top:26px;display:flex;align-items:center;gap:9px;font-weight:700;font-size:15px;color:var(--ink)}
.contact-email{left:498px}
.contact-phone{left:696px}
.contact-icon{width:29px;height:29px;border-radius:50%;background:var(--amber);display:flex;align-items:center;justify-content:center}
.menu-toggle{left:872px;top:28px;width:28px;height:25px;border:1.5px solid var(--amber);background:#fff;padding:5px 4px;display:flex;flex-direction:column;justify-content:space-between}
.menu-toggle span{display:block;height:1.5px;background:var(--amber)}

/* hero */
.hero{left:0;top:81px;width:940px;height:329px;background:linear-gradient(90deg,#bfd6ec 0%,#5e93c4 45%,var(--hero-blue) 60%,#1f5a92 100%)}
.hero-visual{left:0;top:0;width:470px;height:329px;background:radial-gradient(ellipse at 48% 40%,#ffffff 0%,#f2b7a9 22%,#7fb3d9 55%,rgba(95,148,196,0) 80%)}
.hero-title{left:514px;top:98px;width:400px;font-weight:700;font-size:22px;line-height:33px;color:#fff;text-transform:uppercase;letter-spacing:.2px}
.btn-start{left:514px;top:178px;width:138px;height:33px;background:var(--amber);border:1.5px solid #fff;font-weight:700;font-size:17px;color:var(--ink);display:flex;align-items:center;justify-content:center}
.slider-dots{display:flex;gap:5px}
.slider-dots span{width:7px;height:7px;border-radius:50%;background:#cfd9e4}
.slider-dots span.on{background:var(--ink)}
.hero-dots{left:514px;top:228px}

/* section title */
.section-title{left:0;width:940px;text-align:center;font-weight:900;font-size:25px;letter-spacing:.3px}
.title-rule{height:1px;background:#c8c8c8}
.title-rule i{position:absolute;top:0;height:2px;background:var(--green)}

/* about */
.about-title{top:438px}
.about-title .accent{color:var(--orange)}
.about-title .main{color:var(--ink)}
.about-rule{left:279px;top:478px;width:382px}
.about-rule i{left:136px;width:110px}
.about-text{left:48px;top:500px;width:844px;text-align:center;font-size:11.7px;line-height:22px;color:var(--text)}

/* services */
.services{left:0;top:591px;width:940px;height:271px;background:linear-gradient(#efefef,#fbfbfb)}
.service-card{top:39px;width:259px;height:194px}
.service-media{left:0;top:0;width:259px;height:158px;border-top:3px solid var(--orange)}
.media-design{background:linear-gradient(135deg,#6b4a33,#c9b7a6 55%,#3a2a1f)}
.media-app{background:linear-gradient(135deg,#1a4d9c,#3d86d6 55%,#0f3574)}
.media-idea{background:linear-gradient(135deg,#dfe4ea,#f4f1e6 55%,#c9ced6)}
.service-name{left:0;top:128px;width:259px;height:30px;background:rgba(20,20,20,.85);color:#fff;font-family:"Ubuntu",sans-serif;font-weight:500;font-size:15px;display:flex;align-items:center;justify-content:center}
.service-desc{left:0;top:158px;width:259px;height:36px;background:var(--card-text);font-size:11px;line-height:13px;text-align:center;padding-top:4px;color:var(--text);letter-spacing:.2px}

/* testimonials */
.clients{left:0;top:862px;width:940px;height:264px;background:var(--orange)}
.clients-title{top:22px}
.clients-title .main{color:var(--ink)}
.clients-title .accent{color:#fff}
.clients-rule{left:279px;top:64px;width:374px;background:#fbd5bc}
.clients-rule i{left:132px;width:110px;background:#8a9a3a}
.quote-box{left:180px;top:101px;width:652px;height:122px;border:1px solid #f7a877;border-radius:9px}
.avatar{left:107px;top:109px;width:108px;height:108px;border-radius:50%;background:var(--orange-dark);padding:7px}
.avatar div{width:100%;height:100%;border-radius:50%;background:linear-gradient(160deg,#e9eef3,#b9c6d3)}
.quote-text{left:232px;top:119px;width:588px;font-style:italic;font-size:14px;line-height:19.5px;color:#fff}
.quote-mark{font-family:"Lato",sans-serif;font-weight:900;font-style:normal;font-size:34px;line-height:10px;color:#f7ad7f;vertical-align:-12px}
.quote-author{left:560px;top:195px;width:245px;text-align:right;font-weight:700;font-size:13.5px;color:#fff}
.clients-dots{left:449px;top:228px}
.clients-dots span{background:#fff}
.clients-dots span.on{background:var(--green)}

/* footer */
.site-footer{left:0;top:1126px;width:940px;height:74px;background:var(--footer)}
.social{left:0;top:18px;width:940px;display:flex;justify-content:center;align-items:center;font-size:11px;font-weight:700;color:#b0b0b0}
.social span{padding:0 10px;border-left:1px solid #555}
.social span:first-child{border-left:0;color:#2f7bd4}
.copyright{left:0;top:48px;width:940px;text-align:center;font-size:11px;color:var(--footer-text);letter-spacing:.2px}
</style>
</head>
<body>

<header class="site-header abs">
  <div class="brand abs"><span class="brand-mark"></span><span class="brand-name">KOLVARIN</span></div>
  <div class="contact contact-email abs">
    <span class="contact-icon"><svg width="15" height="11" viewBox="0 0 15 11"><rect x="0.5" y="0.5" width="14" height="10" fill="none" stroke="#fff" stroke-width="1.3"/><path d="M0.5 0.5 L7.5 6 L14.5 0.5" fill="none" stroke="#fff" stroke-width="1.3"/></svg></span>
    info@kolvarinlink.com
  </div>
  <div class="contact contact-phone abs">
    <span class="contact-icon"><svg width="14" height="14" viewBox="0 0 24 24"><path fill="#fff" d="M6.6 10.8c1.4 2.8 3.8 5.1 6.6 6.6l2.2-2.2c.3-.3.7-.4 1-.2 1.1.4 2.3.6 3.6.6.6 0 1 .4 1 1V20c0 .6-.4 1-1 1C10.6 21 3 13.4 3 4c0-.6.4-1 1-1h3.5c.6 0 1 .4 1 1 0 1.3.2 2.5.6 3.6.1.3 0 .7-.2 1z"/></svg></span>
    555-014-7290
  </div>
  <div class="menu-toggle abs"><span></span><span></span><span></span><span></span></div>
</header>

<section class="hero abs">
  <div class="hero-visual abs" role="img" aria-label="Cupped hands holding a sphere of colourful image tiles radiating light"></div>
  <h1 class="hero-title abs">Loren ipsum dolor sit amet sie consectetuer adipiscing</h1>
  <div class="btn-start abs">GET STARTED</div>
  <div class="slider-dots hero-dots abs"><span class="on"></span><span></span><span></span></div>
</section>

<h2 class="section-title about-title abs"><span class="accent">ABOUT</span> <span class="main">KOLVARIN LINK</span></h2>
<div class="title-rule about-rule abs"><i></i></div>
<p class="about-text abs">Lorem ipsum dolor sit amet, consectetuer adipiscing elit, sed diam nonummy nibh euismod tincidunt ut laoreet dolore magna aliquam erat volutpat. Ut wisi enim ad minim veniam, quis nostrud exerci tation ullamcorper suscipit lobortis nisl ut aliquip ex ea commodo consequat. Duis autem vel eum iriure dolor in hendrerit in vulputate velit esse molestie consequat, vel illum dolore eu feugiat nulla facilisis at vero eros et accumsan et iusto o</p>

<section class="services abs">
  <article class="service-card abs" style="left:42px">
    <div class="service-media media-design abs" role="img" aria-label="Laptop showing a website on a wooden desk"></div>
    <h3 class="service-name abs">Creative Design</h3>
    <p class="service-desc abs">Eaque ipsa quae ab illo inventore veritatis<br>et quasi architecto beatae vitae</p>
  </article>
  <article class="service-card abs" style="left:341px">
    <div class="service-media media-app abs" role="img" aria-label="Hand holding a phone with colourful app icons floating above"></div>
    <h3 class="service-name abs">App Development</h3>
    <p class="service-desc abs">Eaque ipsa quae ab illo inventore veritatis<br>et quasi architecto beatae vitae</p>
  </article>
  <article class="service-card abs" style="left:640px">
    <div class="service-media media-idea abs" role="img" aria-label="Hand drawing a glowing light bulb among drafting tools"></div>
    <h3 class="service-name abs">New Product Innovation</h3>
    <p class="service-desc abs">Eaque ipsa quae ab illo inventore veritatis<br>et quasi architecto beatae vitae</p>
  </article>
</section>

<section class="clients abs">
  <h2 class="section-title clients-title abs"><span class="main">WHAT</span> <span class="accent">OUR CLIENTS SAY</span></h2>
  <div class="title-rule clients-rule abs"><i></i></div>
  <div class="quote-box abs"></div>
  <div class="avatar abs"><div role="img" aria-label="Portrait photo of the client"></div></div>
  <p class="quote-text abs"><span class="quote-mark">&ldquo;</span> Lorem ipsum dolor sit amet, consectetuer adipiscing elit, sed diam nonummy nibh euismod tincidunt ut laoreet dolore magna aliquam erat volutpat. Ut wisi enim ad minim veniam, quis nostrud exerci tation ullamcorper suscipit. Lorem ipsum dolor sit amet, consectetuer adipiscing elit. diam nonummy nibh euismod tincsetr. <span class="quote-mark">&rdquo;</span></p>
  <p class="quote-author abs">- Consectetue Radipiscing</p>
  <div class="slider-dots clients-dots abs"><span class="on"></span><span></span><span></span><span></span></div>
</section>

<footer class="site-footer abs">
  <div class="social abs"><span>mirtavel</span><span>plimber</span><span>trelvanet</span><span>vendoloop</span></div>
  <p class="copyright abs">COPYRIGHT &copy; 2016 KOLVARIN LINK. ALL RIGHT RESERVED</p>
</footer>

</body>
</html>
```